Business Card Design

We provide services doing multiple jobs in the construction industry.Please note: The company name needs to be ROCK SOLID BUILDING SERVICESAttached logo was an example of what we wanted. Can you change up the colors?

Industry/Entity Type

Construction

Contact Information for Business Card

ROCK SOLID BUILDING SERVICES5401 HUDSON BEND RDAUSTIN, TX 78734(512)243-6854ROCKSOLIDBUILDINGSERVICES@GMAIL.COM

```html
<!DOCTYPE html>
<html lang="en">
<head>
<meta charset="utf-8">
<title>Pearlwood Framing Works – Business Card</title>
<link rel="stylesheet" href="https://fonts.googleapis.com/css2?family=Arimo:wght@400;700&display=swap">
<style>
  :root {
    --backdrop: #e6e6e6;
    --card: #ffffff;
    --ink: #111111;
    --band: #150b13;
    --band-text: #ffffff;
    --rule: #3a3a6a;
    --brand: #111111;
  }
  * { box-sizing: border-box; margin: 0; padding: 0; }
  html, body {
    width: 1200px;
    height: 817px;
    overflow: hidden;
    background: var(--backdrop);
    font-family: "Arimo", Arial, sans-serif;
    color: var(--ink);
  }
  .stage {
    width: 1200px;
    height: 817px;
    display: flex;
    align-items: center;
    justify-content: center;
  }
  .card {
    position: relative;
    width: 880px;
    height: 503px;
    background: var(--card);
    box-shadow: 0 6px 24px rgba(0,0,0,0.18);
    overflow: hidden;
  }
  .card__body {
    position: absolute;
    inset: 0 0 96px 0;
    display: flex;
  }
  .brand-area {
    width: 50%;
    display: flex;
    align-items: flex-end;
    justify-content: center;
    padding-bottom: 70px;
  }
  .brand-name {
    font-weight: 700;
    font-size: 26px;
    letter-spacing: 1px;
    color: var(--brand);
    text-align: center;
    line-height: 1.25;
  }
  .divider {
    width: 1px;
    background: var(--rule);
    margin-top: 36px;
  }
  .details {
    flex: 1;
    position: relative;
    padding: 60px 0 0 60px;
  }
  .company {
    font-size: 25px;
    font-weight: 400;
    letter-spacing: 0.2px;
  }
  .contact {
    position: absolute;
    left: 60px;
    bottom: 14px;
    list-style: none;
    font-size: 18px;
    line-height: 1.55;
  }
  .contact li { display: flex; align-items: center; gap: 10px; white-space: nowrap; }
  .contact svg { width: 14px; height: 14px; flex: none; fill: var(--ink); }
  .band {
    position: absolute;
    left: 0; right: 0; bottom: 0;
    height: 96px;
    background: var(--band);
    color: var(--band-text);
    display: flex;
    align-items: center;
    padding-left: 36px;
    font-size: 30px;
    letter-spacing: 0.3px;
  }
</style>
</head>
<body>
<main class="stage">
  <article class="card">
    <div class="card__body">
      <div class="brand-area">
        <p class="brand-name">PEARLWOOD<br>FRAMING WORKS</p>
      </div>
      <div class="divider"></div>
      <div class="details">
        <h1 class="company">PEARLWOOD FRAMING WORKS</h1>
        <ul class="contact">
          <li>
            <svg viewBox="0 0 24 24" aria-hidden="true"><path d="M6.6 10.8a15.1 15.1 0 0 0 6.6 6.6l2.2-2.2a1 1 0 0 1 1-.25 11.4 11.4 0 0 0 3.6.57 1 1 0 0 1 1 1V20a1 1 0 0 1-1 1A17 17 0 0 1 3 4a1 1 0 0 1 1-1h3.5a1 1 0 0 1 1 1c0 1.25.2 2.45.57 3.57a1 1 0 0 1-.25 1z"/></svg>
            (512)555-0193
          </li>
          <li>
            <svg viewBox="0 0 24 24" aria-hidden="true"><path d="M2 5h20v14H2z M3.5 6.5v.6l8.5 6 8.5-6v-.6z" fill-rule="evenodd"/></svg>
            Pearlwoodframingworks@mailnest.example
          </li>
        </ul>
      </div>
    </div>
    <footer class="band">7732 FERNGLEN PASS LN AUSTIN, TX 78734</footer>
  </article>
</main>
</body>
</html>
```